Laser Tattoo Removal Business Cards

We are looking for a professional business card design for a laser tattoo removal business. Ideally looking for a black business card design. The name of the business is Brightline Tattoo Removal. We place our cards at local tattoo shops so we ideally are looking for something trendy/edgy to draw both male and female clientele in.

Target Market(s)

Male/Female ages 18-60

Contact Information for Business Card

black background ideally.. hoping to stay within greys, whites and black

Font styles to use
Serif
Sans Serif

Colors
121212
a9a9a9
5c5c5c
f5f5f5
ffffff
7f7f7f
606060
848484
9d9d9d

Requirements
Must have
• Employee Info:
• Melissa Thornbury
• Chief Executive Offer
• m: 919.537.2846
• w: 919.362.4178
• f: 919.685.3907
• mthornbury@brightlinetattooremoval.example
• Address:
• 4615 Oakmere Pkwy, Suite 210
• Raleigh, NC 27654
• Website:
• www.brightlinetattooremoval.example
Nice to have
• Myabe business name on back or logo on back and employee info on the front

```html
<!DOCTYPE html>
<html lang="en">
<head>
<meta charset="utf-8">
<title>Brightline Tattoo Removal – Business Card</title>
<link href="https://fonts.googleapis.com/css2?family=Roboto:wght@400;500&display=swap" rel="stylesheet">
<style>
  :root {
    --ink: #121212;
    --silver: #dcdcdc;
    --silver-edge: #8a8a8a;
    --logo-dark: #2a2a2a;
    --logo-light: #b8b8b8;
    --white: #ffffff;
    --soft-white: #f5f5f5;
    --rule: #7f7f7f;
    --backdrop: #9d9d9d;
  }
  * { box-sizing: border-box; margin: 0; padding: 0; }
  html, body {
    width: 1105px; height: 1200px; overflow: hidden;
    background: var(--backdrop);
    font-family: "Roboto", Arial, sans-serif;
  }
  .canvas { position: relative; width: 1105px; height: 1200px; }
  .card {
    position: absolute; left: 180px; width: 746px; height: 425px;
    background: var(--ink); overflow: hidden;
  }
  .card--front { top: 118px; }
  .card--back { top: 640px; }
  .card__shape { position: absolute; inset: 0; }
  .brand-name {
    position: absolute; left: 0; right: 0; text-align: center;
    font-weight: 500; font-size: 30px; letter-spacing: 4px;
    text-transform: uppercase;
  }
  .card--front .brand-name { top: 70px; color: var(--logo-dark); }
  .card--back .brand-name { top: 190px; color: var(--logo-light); }
  .holder {
    position: absolute; left: 0; right: 0; top: 250px; text-align: center;
    color: var(--white);
  }
  .holder__name { font-size: 22px; font-weight: 500; letter-spacing: 0.5px; text-transform: uppercase; }
  .holder__title-row {
    display: flex; align-items: center; justify-content: center; gap: 12px;
    margin: 2px 66px 0;
  }
  .holder__rule { flex: 1; height: 1px; background: var(--rule); }
  .holder__title { font-size: 16px; color: var(--soft-white); }
  .contact { position: absolute; left: 0; right: 0; text-align: center; color: var(--white); font-size: 14.5px; }
  .contact--phones { top: 322px; }
  .contact--web { top: 348px; }
  .contact--address { top: 379px; }
  .contact__item { display: inline-flex; align-items: center; gap: 5px; margin: 0 4px; }
  .contact__icon { width: 13px; height: 13px; fill: var(--white); }
  .website {
    position: absolute; left: 0; right: 0; top: 362px; text-align: center;
    color: var(--soft-white); font-size: 16px; letter-spacing: 3px;
  }
</style>
</head>
<body>
<main class="canvas">

  <section class="card card--front">
    <svg class="card__shape" viewBox="0 0 746 425" width="746" height="425">
      <rect width="746" height="425" fill="var(--silver)"/>
      <path d="M0,138 Q373,322 746,138 L746,425 L0,425 Z" fill="var(--silver-edge)"/>
      <path d="M0,150 Q373,306 746,150 L746,425 L0,425 Z" fill="var(--ink)"/>
    </svg>
    <p class="brand-name">Brightline Tattoo Removal</p>

    <div class="holder">
      <h1 class="holder__name">Melissa Thornbury</h1>
      <div class="holder__title-row">
        <span class="holder__rule"></span>
        <span class="holder__title">Chief Executive Offer</span>
        <span class="holder__rule"></span>
      </div>
    </div>

    <p class="contact contact--phones">
      <span class="contact__item">
        <svg class="contact__icon" viewBox="0 0 16 16"><path d="M3.6 1l2.4 3-1.4 1.6c.8 2 2.6 3.9 4.8 4.8L11 9l3 2.4-1.4 2.8C7 14 2 9 1.8 3z"/></svg>919.362.4178</span>
      <span class="contact__item">
        <svg class="contact__icon" viewBox="0 0 16 16"><path d="M4 0h8v16H4z M5.5 2v10h5V2z"/></svg>919.537.2846</span>
      <span class="contact__item">
        <svg class="contact__icon" viewBox="0 0 16 16"><path d="M4 1h8v4H4z M1 6h14v7h-3v2H4v-2H1z M5.5 10v3.5h5V10z"/></svg>919.685.3907</span>
    </p>
    <p class="contact contact--web">
      <span class="contact__item">
        <svg class="contact__icon" viewBox="0 0 16 16"><path d="M1 3h14v10H1z M1.5 3.5 8 9l6.5-5.5" stroke="var(--ink)" stroke-width="1.2"/></svg>mthornbury@brightlinetattooremoval.example</span>
      <span class="contact__item">
        <svg class="contact__icon" viewBox="0 0 16 16"><circle cx="8" cy="8" r="7"/><path d="M1 8h14M8 1c-3 3-3 11 0 14M8 1c3 3 3 11 0 14" stroke="var(--ink)" stroke-width="1" fill="none"/></svg>www.brightlinetattooremoval.example</span>
    </p>
    <p class="contact contact--address">4615 Oakmere Pkwy, Suite 210, Raleigh, NC 27654</p>
  </section>

  <section class="card card--back">
    <p class="brand-name">Brightline Tattoo Removal</p>
    <p class="website">www.brightlinetattooremoval.example</p>
  </section>

</main>
</body>
</html>
```